Quorva - corporate Business Card

We need a good look and innovative business card for a new start up company based in Los Angeles called "Quorva". We are in a payment business, including payment card, app, and ewallet. We are expert in online payment and Card not present (CNP) transaction.
We need an innovative, modern business card.

Our logo font is Aero Matics

Target Market(s)

Startup - Bank - Online Payment - Card Manufacturing

Industry/Entity Type

Startup

Contact Information for Business Card

phone: 555 014 7396 - Address: 4172 Marlowe blvd, Tarrow Heights, NV 89014

Requirements
Must have
• Message: innovative, professional, expert, high tech, trust, online payment expert, security
Nice to have
• no comment
Should not have
• no Comment

```html
<!DOCTYPE html>
<html lang="en">
<head>
<meta charset="utf-8">
<title>Quorva business card</title>
<link href="https://fonts.googleapis.com/css2?family=Exo+2:wght@700&family=Lato:wght@400;700&display=swap" rel="stylesheet">
<style>
  :root {
    --brand-red: #b01c2c;
    --card-white: #ffffff;
    --accent-grey: #3a3a3a;
    --page-bg: #e6e6e6;
    --text-light: #ffffff;
  }
  * { margin: 0; padding: 0; box-sizing: border-box; }
  html, body { width: 1200px; height: 900px; overflow: hidden; }
  body {
    background: var(--page-bg);
    display: flex;
    flex-direction: column;
    align-items: center;
    justify-content: center;
    gap: 60px;
    font-family: "Lato", Arial, sans-serif;
  }
  .card {
    position: relative;
    width: 630px;
    height: 360px;
    border-radius: 22px;
    overflow: hidden;
    background: var(--brand-red);
    color: var(--text-light);
  }
  .front-brand {
    position: absolute;
    left: 150px;
    top: 138px;
    display: flex;
    align-items: center;
    gap: 16px;
  }
  .brand-dot {
    width: 74px;
    height: 74px;
    border-radius: 50%;
    background: var(--card-white);
  }
  .brand-name {
    font-family: "Exo 2", Arial, sans-serif;
    font-weight: 700;
    font-size: 68px;
    letter-spacing: 1px;
    line-height: 1;
    color: var(--text-light);
  }
  .front-web {
    position: absolute;
    right: 150px;
    top: 245px;
    font-size: 14px;
    letter-spacing: 0.5px;
  }
  .back-shape { position: absolute; inset: 0; }
  .back-brand {
    position: absolute;
    left: 34px;
    top: 152px;
    display: flex;
    align-items: center;
    gap: 10px;
  }
  .back-brand .brand-dot {
    width: 54px;
    height: 54px;
    background: var(--brand-red);
  }
  .back-brand .brand-name {
    font-size: 46px;
    color: var(--brand-red);
  }
  .contact {
    position: absolute;
    left: 405px;
    top: 62px;
    font-size: 13px;
    line-height: 1.5;
  }
  .contact-name { font-size: 18px; font-weight: 400; letter-spacing: 0.5px; line-height: 1.2; }
  .contact-role { font-size: 13px; margin-bottom: 16px; }
  .contact-address { margin-bottom: 16px; }
  .contact-line { display: flex; align-items: center; gap: 8px; }
  .contact-line svg { width: 12px; height: 12px; flex: none; }
</style>
</head>
<body>

<section class="card card-front" aria-label="Card front">
  <div class="front-brand">
    <span class="brand-dot"></span>
    <span class="brand-name">quorva</span>
  </div>
  <p class="front-web">www.quorva.com</p>
</section>

<section class="card card-back" aria-label="Card back">
  <svg class="back-shape" viewBox="0 0 630 360" preserveAspectRatio="none" aria-hidden="true">
    <path d="M0,0 H300 Q440,170 335,360 H0 Z" fill="var(--card-white)"/>
    <path d="M300,0 Q450,170 335,360 Q428,170 288,0 Z" fill="var(--accent-grey)"/>
  </svg>
  <div class="back-brand">
    <span class="brand-dot"></span>
    <span class="brand-name">quorva</span>
  </div>
  <div class="contact">
    <h2 class="contact-name">DAREN HOLT</h2>
    <p class="contact-role">President</p>
    <p class="contact-address">Address:<br>4172 Marlowe blvd<br>Tarrow Heights, NV 89014</p>
    <p class="contact-line">
      <svg viewBox="0 0 12 12"><path d="M2.5 1 L4.5 1 L5 3.5 L3.8 4.4 Q4.8 6.8 7.6 8.2 L8.5 7 L11 7.5 L11 9.5 Q10.5 11 9 11 Q1 9.5 1 2.5 Q1 1 2.5 1 Z" fill="currentColor"/></svg>
      555 014 7396
    </p>
    <p class="contact-line">
      <svg viewBox="0 0 12 12"><rect x="0.5" y="2" width="11" height="8" fill="currentColor"/><path d="M0.5 2 L6 6.5 L11.5 2" stroke="var(--brand-red)" stroke-width="1" fill="none"/></svg>
      info@quorva.com
    </p>
    <p class="contact-line">
      <svg viewBox="0 0 12 12"><circle cx="6" cy="6" r="5" fill="none" stroke="currentColor" stroke-width="1.2"/><path d="M1 6 H11 M6 1 Q3 6 6 11 M6 1 Q9 6 6 11" stroke="currentColor" stroke-width="0.9" fill="none"/></svg>
      www.quorva.com
    </p>
  </div>
</section>

</body>
</html>
```